Thornbury Spa

We are a large Miami Beach spa and salon. I am still building our website but you can use it as a resource to gain a better understanding of who we are ....www.velloraspa-studio.com.

We offer a comprehensive list of services in hair, nails, massage, skin care, tanning, spray tanning and waxing and we offer high quality products for skin care, tanning and hair. We are open 7 days.

We would like to see a clean and simple menu that looks a lot like the one from "The Spa at Larkwood." In particular, we have a copy of a menu from their West Hollywood, CA location that is just beautiful. In the uploaded content you will see a sampling of that menu. We would like to see greys, blacks, silvers, whites and warm colors like reds and oranges. We specifically attempt to remain gender neutral so that we don't attract only girls (with pink colors and flowers etc). The final design should convey a simple, clean, friendly environment and the final product should be sized such that it is 1.) portable and 2.) inexpensive to print. We will be running thousands of these at a time so cost of printing is a consideration.

The booklet consists of two parts: one part is the standard menu with descriptions of services and products and photos etc (think of this as the sales piece that convinces a potential customer to visit) and will be stapled together like you would expect a small menu to be and should resemble the Larkwood menu. The prices should not be included in this part of the booklet that will be printed and stapled. The other part is a single insert and is removable and replaceable. I want this removable insert placed in the last page of the book in a folder pocket or something else that you can think of so that when it's time to change prices here that I am not throwing away all of the booklets....I am only replacing the inserts at the end of the menu booklet. Please design this single page insert so that should a customer remove it from the booklet and keep it, that it stands alone with our name, logo, website and phone number. This page can and probably will have to be 2 sided.

At the back of the booklet, I also want the polices to be printed in one page (think fine print in any sort of business dealing.)

With regard to the look and feel slider of economical v upmarket...we definitely want to convey we deliver upmarket services at reasonable prices. Think, world class services and products at reasonable, everyday prices.

With regard to the uploaded files:
I uploaded both EPS and TIF formats. The colors in those files are not the palette we want at all. The colors we want use for the circular logo must match the standard colors as depicted in the uploaded file "Thornburytanrooms"

Target Market(s)

The target market is the average 20-35 year old in Miami Beach that cares about their appearance. The range of clientele is quite diverse.

Industry/Entity Type

Environment

Requirements
Must have
• It must have elegant and simple photographs that relate to the services being offered. We are selling a service set and an environment...so this menu should be reflect that goal. The logo should be repeated often throughout the book but in subtle ways.

Stock photos are fine as long as they don't seem obviously stock.

Should not have
• Nothing buddha like. Nothing themed. It should be all inclusive and not seek to identify with any particular group or gender.

Nothing that fits the stereotype of "Miami Beach." We want to represent ourselves in the same category as the best spas in the world because we moving everything we do in that direction. Think class!

```html
<!DOCTYPE html>
<html lang="en">
<head>
<meta charset="utf-8">
<title>Thornbury Spa – Menu Cover</title>
<link rel="stylesheet" href="https://fonts.googleapis.com/css2?family=Crimson+Text:wght@400;600&display=swap">
<style>
  :root {
    --charcoal: #2f2f31;
    --charcoal-glass: rgba(38, 38, 40, 0.8);
    --ember: #c4502b;
    --silver: #9c9ea2;
    --grey: #7d7d80;
    --ink: #3a3a3c;
    --white: #ffffff;
    --band-text: #e4e4e6;
  }
  * { margin: 0; padding: 0; box-sizing: border-box; }
  html, body { width: 1200px; height: 389px; overflow: hidden; background: var(--white); }
  body { font-family: "Crimson Text", Georgia, serif; }

  .cover { position: relative; width: 1200px; height: 389px; }

  /* Back panel */
  .back-panel { position: absolute; left: 0; top: 0; width: 600px; height: 389px; }
  .hours { position: absolute; left: 0; width: 600px; top: 50px; text-align: center; line-height: 1.15; }
  .hours__title { color: var(--ink); font-size: 13px; }
  .hours__days { color: var(--ink); font-size: 13px; text-transform: uppercase; margin-top: 1px; }
  .hours__time { color: var(--ember); font-size: 13px; }
  .hours__days--sunday { margin-top: 6px; }

  .brand { position: absolute; text-align: center; }
  .brand__mark { display: block; margin: 0 auto 5px; border-radius: 50%; border: 2px solid var(--silver); }
  .brand__name { color: var(--silver); text-transform: uppercase; line-height: 1.05; }
  .brand__word { display: block; }
  .brand__word--sub { letter-spacing: 8px; margin-right: -8px; }

  .back-brand { left: 0; width: 600px; top: 176px; }
  .back-brand .brand__mark { width: 34px; height: 34px; }
  .back-brand .brand__name { font-size: 20px; letter-spacing: 2px; }
  .back-brand .brand__word--sub { font-size: 20px; }
  .brand__tagline { color: var(--grey); font-size: 13px; margin-top: 8px; letter-spacing: 0.3px; }

  /* Front panel */
  .front-panel { position: absolute; left: 600px; top: 0; width: 600px; height: 389px; }
  .front-panel__photo {
    position: absolute; inset: 0;
    background:
      radial-gradient(ellipse 170px 120px at 330px 110px, #e6c3ab 0%, rgba(230,195,171,0) 100%),
      radial-gradient(ellipse 230px 150px at 180px 300px, #221c1a 0%, rgba(34,28,26,0) 100%),
      radial-gradient(ellipse 80px 50px at 440px 340px, #d2522e 0%, rgba(210,82,46,0) 100%),
      radial-gradient(ellipse 60px 40px at 150px 280px, #c9462f 0%, rgba(201,70,47,0) 100%),
      linear-gradient(160deg, #f6f4f2 0%, #eee1d7 45%, #dbbca6 70%, #f3eeea 100%);
  }
  .front-brand { right: 36px; top: 22px; width: 132px; }
  .front-brand .brand__mark { width: 30px; height: 30px; }
  .front-brand .brand__name { font-size: 19px; letter-spacing: 1.5px; }

  /* Band */
  .band { position: absolute; left: 0; top: 314px; width: 1200px; height: 44px; }
  .band__back { position: absolute; left: 0; top: 0; width: 600px; height: 44px; background: var(--charcoal); }
  .band__front { position: absolute; left: 600px; top: 0; width: 600px; height: 44px; background: var(--charcoal-glass); }
  .band__contact { position: absolute; left: 0; width: 600px; top: 9px; text-align: center; color: var(--band-text); font-size: 9.5px; line-height: 1.35; }
  .band__slogan { position: absolute; left: 52px; top: 12px; color: var(--white); font-size: 13px; }
  .band__divider { position: absolute; left: 308px; top: 7px; width: 1px; height: 30px; background: rgba(255,255,255,0.6); }
  .band__tagline { position: absolute; left: 330px; top: 12px; color: var(--white); font-size: 13px; }
</style>
</head>
<body>
<main class="cover">
  <section class="back-panel">
    <div class="hours">
      <p class="hours__title">{ Salon Hours }</p>
      <p class="hours__days">Monday - Saturday</p>
      <p class="hours__time">9:00 am. - 5:00 pm.</p>
      <p class="hours__days hours__days--sunday">Sunday</p>
      <p class="hours__time">10:00 am. - 4:00 pm.</p>
    </div>
    <div class="brand back-brand">
      <span class="brand__mark"></span>
      <p class="brand__name"><span class="brand__word">Thornbury</span><span class="brand__word brand__word--sub">Spa</span></p>
      <p class="brand__tagline">Relaxing... Therapeutic... Soothing... SPA</p>
    </div>
  </section>

  <section class="front-panel">
    <div class="front-panel__photo" role="img" aria-label="Photograph of a relaxed guest receiving a gentle head massage, dark hair spread with flowers"></div>
    <div class="brand front-brand">
      <span class="brand__mark"></span>
      <p class="brand__name"><span class="brand__word">Thornbury</span><span class="brand__word brand__word--sub">Spa</span></p>
    </div>
  </section>

  <div class="band">
    <div class="band__back">
      <p class="band__contact">Coral Vista Court, 2200 Palm Lane #4, Miami Beach, Florida<br>Call Us : 305.555.0148, www.velloraspa-studio.com</p>
    </div>
    <div class="band__front">
      <p class="band__slogan">{ Rejuvenate your body, mind and senses }</p>
      <span class="band__divider"></span>
      <p class="band__tagline">Relaxing... Therapeutic... Soothing... SPA</p>
    </div>
  </div>
</main>
</body>
</html>
```